Vantoq Business Card Project showing the logo and a marbo image on the rear

Design a whacky but professional business card, the logo is for the front and the Marbo image is for the rear. Happy to consider other open source Marbo Images if the designer wants to select one from the web. Vantoq is a competitor to OMB.com.au and Pellory.com.au and is based around every property in Australia

Target Market(s)

Business

Contact Information for Business Card

Name, Title, Email, Web, Phone Number

Font styles to use
Other font styles liked:
• avenir

Requirements
Must have
• Image on Back logo on front
Nice to have
• Happy to consider other images on rear, preftably Colin Marbo. Image supplied I own, we can use open source other Marbo Images

```html
<!DOCTYPE html>
<html lang="en">
<head>
<meta charset="utf-8">
<title>Vantoq Business Card</title>
<link href="https://fonts.googleapis.com/css2?family=Nunito+Sans:wght@700;800&family=Roboto:wght@400&display=swap" rel="stylesheet">
<style>
  :root {
    --stage: #262626;
    --card: #efefef;
    --ink: #151515;
    --body: #1f1f1f;
    --orange: #ec8a12;
    --night: #3b3c3f;
  }
  * { margin: 0; padding: 0; box-sizing: border-box; }
  html, body { width: 1138px; height: 1200px; overflow: hidden; background: var(--stage); }
  .canvas { position: relative; width: 1138px; height: 1200px; }

  .card {
    position: absolute;
    width: 376px;
    height: 621px;
    border-radius: 14px;
    overflow: hidden;
  }
  .card--back { left: 155px; top: 275px; }
  .card--front { left: 577px; top: 274px; background: var(--card); text-align: center; }

  .artwork {
    width: 100%;
    height: 100%;
    background:
      linear-gradient(180deg, rgba(0,0,0,0) 0%, rgba(0,0,0,0) 52%, #d9407e 66%, #e8d33a 82%, #6bbf3a 100%),
      linear-gradient(90deg, var(--orange) 0%, var(--orange) 49.5%, var(--night) 50%, var(--night) 100%);
  }

  .wordmark {
    position: absolute;
    top: 164px;
    left: 0; right: 0;
    display: flex;
    justify-content: center;
    align-items: center;
    gap: 12px;
  }
  .wordmark__square { width: 26px; height: 26px; background: var(--orange); }
  .wordmark__name {
    font-family: "Nunito Sans", sans-serif;
    font-weight: 800;
    font-size: 38px;
    line-height: 46px;
    color: var(--ink);
    letter-spacing: 0.5px;
  }

  .person { position: absolute; top: 313px; left: 0; right: 0; }
  .person__name {
    font-family: "Nunito Sans", sans-serif;
    font-weight: 800;
    font-size: 25px;
    line-height: 30px;
    color: var(--ink);
  }
  .person__title {
    font-family: "Roboto", sans-serif;
    font-size: 16px;
    line-height: 22px;
    color: var(--orange);
    margin-top: 4px;
  }

  .divider { position: absolute; top: 397px; left: 0; width: 376px; height: 30px; }

  .contact {
    position: absolute;
    top: 435px;
    left: 0; right: 0;
    font-family: "Roboto", sans-serif;
    font-size: 16px;
    line-height: 23.5px;
    color: var(--body);
  }
  .address {
    position: absolute;
    top: 525px;
    left: 0; right: 0;
    font-family: "Roboto", sans-serif;
    font-size: 16px;
    line-height: 24px;
    color: var(--body);
  }
</style>
</head>
<body>
<div class="canvas">
  <section class="card card--back">
    <div class="artwork" role="img" aria-label="Colourful pop-art city illustration: sun and clouds on orange sky, stars and a plane on night sky, cheerful buildings and a train below"></div>
  </section>

  <section class="card card--front">
    <div class="wordmark">
      <span class="wordmark__square"></span>
      <span class="wordmark__name">Vantoq</span>
    </div>

    <div class="person">
      <div class="person__name">Owen Tallis</div>
      <div class="person__title">Founder &amp; CEO</div>
    </div>

    <svg class="divider" viewBox="0 0 376 30" width="376" height="30" aria-hidden="true">
      <g stroke="var(--orange)" fill="none">
        <line x1="58" y1="15" x2="130" y2="15" stroke-width="2"/>
        <line x1="246" y1="15" x2="318" y2="15" stroke-width="2"/>
        <circle cx="158" cy="15" r="12.5" stroke-width="1.6"/>
        <circle cx="188" cy="15" r="12.5" stroke-width="1.6"/>
        <circle cx="218" cy="15" r="12.5" stroke-width="1.6"/>
      </g>
      <g fill="var(--orange)">
        <path d="M152 18h12v3h-12z M153 14c2-4 8-4 10 0v3h-10z"/>
        <rect x="181.5" y="10" width="13" height="10" rx="1"/>
      </g>
      <path d="M182 10.5l6 5 6-5" stroke="#efefef" stroke-width="1.3" fill="none"/>
      <g stroke="var(--orange)" stroke-width="1.2" fill="none">
        <circle cx="218" cy="15" r="6"/>
        <ellipse cx="218" cy="15" rx="2.6" ry="6"/>
        <line x1="212" y1="15" x2="224" y2="15"/>
      </g>
    </svg>

    <div class="contact">
      <div>(00) 4141 5252</div>
      <div>tallis@vantoq.com</div>
      <div>www.vantoq.com</div>
    </div>

    <div class="address">
      <div>Level 4, 18 Carrow Lane,</div>
      <div>Sydney 2000, Australia</div>
    </div>
  </section>
</div>
</body>
</html>
```